Brivolt Technologies business card design

We need a business card designed with our new logo. it would be great if the card could communicate it is a technology based company.

Target Market(s)

system integrators

Industry/Entity Type

technology, IOT

Contact Information for Business Card

Name, designation, Address, telephone number, email address

Requirements
Must have
• logo and company name
Nice to have
• something to do with technology

```html
<!DOCTYPE html>
<html lang="en">
<head>
<meta charset="utf-8">
<title>Brivolt Technologies business card</title>
<link href="https://fonts.googleapis.com/css2?family=Open+Sans:wght@400;700&display=swap" rel="stylesheet">
<style>
  :root {
    --backdrop: #3b3b3b;
    --card: #161616;
    --card-deep: #0e0e0e;
    --accent: #f7941d;
    --ink: #ffffff;
    --ink-soft: #e6e6e6;
  }
  * { box-sizing: border-box; margin: 0; padding: 0; }
  html, body {
    width: 1200px; height: 801px; overflow: hidden;
    background: var(--backdrop);
    font-family: "Open Sans", sans-serif;
  }
  .sheet {
    width: 1200px; height: 801px;
    display: flex; align-items: center; justify-content: center; gap: 40px;
  }
  .card {
    position: relative;
    width: 520px; height: 297px;
    background: var(--card);
    border: 2px solid var(--accent);
    box-shadow: 0 14px 30px rgba(0,0,0,.45);
    overflow: hidden;
  }
  .wordmark {
    display: flex; align-items: center; gap: 9px;
    color: var(--ink);
    font-weight: 700;
    font-size: 19px;
    letter-spacing: .3px;
    white-space: nowrap;
  }
  .wordmark-square {
    width: 16px; height: 16px; background: var(--accent); flex: none;
  }
  /* front */
  .card-front .wordmark { position: absolute; left: 28px; top: 150px; }
  .divider {
    position: absolute; left: 300px; top: 48px;
    width: 2px; height: 200px; background: var(--accent);
  }
  .contact {
    position: absolute; left: 318px; top: 52px;
    color: var(--ink-soft); font-size: 12.5px; line-height: 1.45;
  }
  .contact-name {
    color: var(--accent); font-weight: 700; font-size: 17px; line-height: 1.2;
  }
  .contact-role { margin-bottom: 12px; }
  .contact-address { margin-bottom: 12px; }
  .contact-line { display: flex; align-items: center; gap: 7px; }
  .contact-line svg { width: 11px; height: 11px; flex: none; }
  /* back */
  .pattern-field {
    position: absolute; inset: 0;
    background: linear-gradient(150deg, var(--card-deep) 0%, #1c1c1c 55%, #2a2a2a 100%);
  }
  .card-back .wordmark { position: absolute; right: 40px; bottom: 82px; }
</style>
</head>
<body>
<main class="sheet">
  <section class="card card-front" aria-label="Business card front">
    <div class="wordmark"><span class="wordmark-square"></span>Brivolt Technologies</div>
    <div class="divider"></div>
    <div class="contact">
      <p class="contact-name">DANIEL ARVANE</p>
      <p class="contact-role">President</p>
      <p class="contact-address">1187 Harbor Crest Way<br>Seal Cove CA 90417</p>
      <p class="contact-line">
        <svg viewBox="0 0 12 12" aria-hidden="true"><circle cx="6" cy="6" r="6" fill="var(--accent)"/><path d="M3.6 3.2l1.3-.3.7 1.5-.8.6c.4.8 1 1.4 1.8 1.8l.6-.8 1.5.7-.3 1.3C5.8 8.2 3.8 6.2 3.6 3.2z" fill="var(--card)"/></svg>
        949-555-0187
      </p>
      <p class="contact-line">
        <svg viewBox="0 0 12 12" aria-hidden="true"><rect x="1" y="2.5" width="10" height="7" fill="var(--accent)"/><path d="M1 2.5l5 4 5-4" fill="none" stroke="var(--card)" stroke-width="1"/></svg>
        info@brivolttech.com
      </p>
      <p class="contact-line">
        <svg viewBox="0 0 12 12" aria-hidden="true"><circle cx="6" cy="6" r="5.5" fill="var(--accent)"/><path d="M.5 6h11M6 .5c-2.5 3-2.5 8 0 11M6 .5c2.5 3 2.5 8 0 11" fill="none" stroke="var(--card)" stroke-width=".8"/></svg>
        www.brivolttech.com
      </p>
    </div>
  </section>

  <section class="card card-back" aria-label="Business card back">
    <div class="pattern-field" role="img" aria-label="Tone-on-tone repeating emblem pattern across the card"></div>
    <div class="wordmark"><span class="wordmark-square"></span>Brivolt Technologies</div>
  </section>
</main>
</body>
</html>
```